Graphic Design for a block-note A4 size

We need a graphic design for a simple block-note A4 size. The product consists of 50 sheets in VERTICAL A4 (21x29,7cm) size, simply glued on top, without cover. We would like to have proposals with double application: one for home users without a logo and one for professionals with an area "put your logo here".
The graphics should be simple and attractive, elegant and pleasant to keep on your desk.
The block-notes may have standard squares (5 or 10 mm) or stripes (10 mm spaced) on the background to make the writing easy.
Feel free to use your creativity, the only limit is the CMYK color space.

We will upload some block-note simple templates and 3D sample images to help you.

Reason: We want to give you more few days to work on your graphic designs.

• The graphics should be simple and attractive, elegant and pleasant to keep on your desk.

• The block-notes may have standard squares (5 or 10 mm) or stripes (10 mm spaced) on the background to make the writing easy.

```html
<!DOCTYPE html>
<html lang="en">
<head>
<meta charset="utf-8">
<title>A4 Block-Note Sheets</title>
<link rel="stylesheet" href="https://fonts.googleapis.com/css2?family=Tenor+Sans&display=swap">
<style>
  :root {
    --backdrop: #0a4f93;
    --sheet: #ffffff;
    --grid-line: #dedede;
    --grid-frame: #d6d6d6;
    --accent-deep: #2f9ae0;
    --accent-bright: #45c0f2;
    --accent-pale: #cfe9f4;
    --logo-text: #6a6a6a;
  }
  * { margin: 0; padding: 0; box-sizing: border-box; }
  html, body {
    width: 1200px;
    height: 848px;
    overflow: hidden;
  }
  body {
    position: relative;
    background: var(--backdrop);
    font-family: "Tenor Sans", "Optima", sans-serif;
  }
  .sheet {
    position: absolute;
    background: var(--sheet);
    overflow: hidden;
  }
  .sheet--home { left: 73px; top: 62px; width: 499px; height: 711px; }
  .sheet--pro  { left: 618px; top: 64px; width: 493px; height: 708px; }

  .writing-grid {
    position: absolute;
    border: 1px solid var(--grid-frame);
    background-image:
      linear-gradient(to right, var(--grid-line) 1px, transparent 1px),
      linear-gradient(to bottom, var(--grid-line) 1px, transparent 1px);
    background-size: 24px 24px;
  }
  .sheet--home .writing-grid { left: 19px; top: 22px; width: 461px; height: 655px; }
  .sheet--pro  .writing-grid { left: 14px; top: 20px; width: 464px; height: 645px; }

  .corner-accent {
    position: absolute;
    left: 0; top: 0;
    width: 100%; height: 100%;
  }

  .logo-slot {
    position: absolute;
    color: var(--logo-text);
    line-height: 1;
  }
  .logo-slot__small { display: block; font-size: 21px; }
  .logo-slot__large { display: block; font-size: 31px; margin-top: 6px; letter-spacing: 0.5px; }
  .sheet--home .logo-slot { left: 374px; top: 609px; }
  .sheet--pro  .logo-slot { left: 28px; top: 603px; }
</style>
</head>
<body>
  <section class="sheet sheet--home" aria-label="Notepad sheet, home edition">
    <div class="writing-grid"></div>
    <svg class="corner-accent" viewBox="0 0 499 711" role="img" aria-label="Scattered blue triangle pattern across the top-left corner">
      <defs>
        <linearGradient id="home-fade" x1="0" y1="0" x2="1" y2="1">
          <stop offset="0" stop-color="#45c0f2" stop-opacity="0.85"/>
          <stop offset="0.45" stop-color="#8fd0f0" stop-opacity="0.55"/>
          <stop offset="1" stop-color="#cfe9f4" stop-opacity="0.2"/>
        </linearGradient>
      </defs>
      <path d="M0 0 H499 V20 L330 35 L200 80 L120 130 L60 190 L25 250 L0 270 Z" fill="url(#home-fade)"/>
    </svg>
    <div class="logo-slot">
      <span class="logo-slot__small">your logo</span>
      <span class="logo-slot__large">HERE</span>
    </div>
  </section>

  <section class="sheet sheet--pro" aria-label="Notepad sheet, professional edition">
    <div class="writing-grid"></div>
    <svg class="corner-accent" viewBox="0 0 493 708" role="img" aria-label="Scattered blue triangle pattern in the top-left and bottom-right corners">
      <defs>
        <linearGradient id="pro-fade-top" x1="0" y1="0" x2="1" y2="1">
          <stop offset="0" stop-color="#45c0f2" stop-opacity="0.8"/>
          <stop offset="0.5" stop-color="#8fd0f0" stop-opacity="0.5"/>
          <stop offset="1" stop-color="#cfe9f4" stop-opacity="0.15"/>
        </linearGradient>
        <linearGradient id="pro-fade-bottom" x1="1" y1="1" x2="0" y2="0">
          <stop offset="0" stop-color="#2f9ae0" stop-opacity="0.85"/>
          <stop offset="0.45" stop-color="#6fc4ef" stop-opacity="0.55"/>
          <stop offset="1" stop-color="#cfe9f4" stop-opacity="0.15"/>
        </linearGradient>
      </defs>
      <path d="M0 0 H400 V12 L250 25 L150 55 L80 100 L35 150 L12 200 L0 210 Z" fill="url(#pro-fade-top)"/>
      <path d="M493 440 V708 H150 L200 690 L330 630 L420 560 L460 490 Z" fill="url(#pro-fade-bottom)"/>
    </svg>
    <div class="logo-slot">
      <span class="logo-slot__small">your logo</span>
      <span class="logo-slot__large">HERE</span>
    </div>
  </section>
</body>
</html>
```